Website for IT consulting Company

I need a website upgrade, the existing site content is ok, I would also like to add a testimonial page, the site should be something that is easy for us to update content. You use the content from www.kelvanbrook.com as an example. I will also post update logo and artwork. I also need a contact form with some type of validation or captcha.

I added Coded to the Project

Please omit Address maps

Target Market(s)

small business, service oriented companies. We provide IT Consulting, support and mangement

Industry/Entity Type

Information Technology

Coding

Number of Pages Required

1 page

Font styles to use
Serif
Sans Serif

Requirements
Must have
• Contain logo attached, and content from existing web site www.kelvanbrook.com.
• Also need to update content easily, and be movable to different platforms.
• There is a catch phrase
• "Let us worry about your technology…” “ so you don’t have to!”
• Should be included.
Nice to have
• Testimonial page, Project page where we can post new and past projects and pictures
Should not have
• none

```html
<!DOCTYPE html>
<html lang="en">
<head>
<meta charset="utf-8">
<title>Kelvanbrook – IT Solutions</title>
<link rel="stylesheet" href="https://fonts.googleapis.com/css2?family=Lato:wght@300;400;700;900&display=swap">
<style>
:root{
  --blue:#29a8e0;
  --blue-dark:#1b8fc4;
  --ink:#333a40;
  --muted:#7b8187;
  --light:#f3f4f6;
  --line:#e2e5e8;
  --white:#ffffff;
  --night:#1d2329;
  --night-2:#2a3139;
}
*{box-sizing:border-box;margin:0;padding:0}
html,body{width:1200px;height:4358px;overflow:hidden}
body{font-family:"Lato",Arial,sans-serif;color:var(--ink);background:var(--white)}
section,header,footer{position:relative;width:1200px;overflow:hidden}
.photo{position:absolute;inset:0}
.center{text-align:center}
.section-title{position:relative;z-index:1;font-size:40px;font-weight:400;letter-spacing:1px;text-align:center;color:var(--blue)}
.divider{position:relative;z-index:1;display:flex;align-items:center;justify-content:center;gap:8px;margin:12px auto 0;width:240px}
.divider span{flex:1;height:1px;background:#c8cdd2}
.divider i{width:10px;height:10px;background:#8a9098;display:block}
.btn{display:inline-block;border:2px solid var(--blue);color:var(--ink);font-size:15px;letter-spacing:1px;padding:0 22px;line-height:40px;background:var(--white)}
.btn-solid{display:inline-block;background:var(--blue);color:var(--white);border:none;font-weight:700;font-size:18px;letter-spacing:1px}

/* hero */
.hero{height:675px}
.hero .photo{background:linear-gradient(180deg,rgba(20,26,32,.72),rgba(20,26,32,.6)),linear-gradient(100deg,#5c6670,#2e353c 45%,#55606a 75%,#3b434b)}
.brand{position:absolute;left:80px;top:22px;display:flex;align-items:center;gap:14px;color:var(--white);font-weight:900;font-size:40px;letter-spacing:2px}
.brand b{width:46px;height:46px;background:var(--blue);display:block}
.menu-btn{position:absolute;right:80px;top:40px;width:40px;height:40px;background:rgba(255,255,255,.85);display:flex;flex-direction:column;justify-content:center;align-items:center;gap:4px}
.menu-btn span{width:16px;height:3px;background:#555}
.hero h1{position:absolute;top:236px;left:0;right:0;text-align:center;color:var(--white);font-size:54px;font-weight:700;line-height:64px;letter-spacing:1px}
.hero p{position:absolute;top:376px;left:240px;right:240px;text-align:center;color:#eef1f3;font-size:17px;line-height:26px}
.hero .btn{position:absolute;top:500px;left:505px;width:190px;height:50px;line-height:46px;text-align:center;background:transparent;border-color:var(--white);color:var(--white);padding:0;font-size:16px}

/* solutions */
.solutions{height:656px;background:#f5f6f7;padding-top:60px}
.cards{position:absolute;top:147px;left:76px;display:flex;gap:22px}
.card{width:335px;height:448px;background:var(--white);box-shadow:0 2px 8px rgba(0,0,0,.12);text-align:center}
.card .img{height:209px}
.card h3{font-size:21px;font-weight:400;color:var(--blue);margin:22px 14px 8px;line-height:24px}
.card p{font-size:13px;line-height:18px;color:var(--muted);padding:0 32px;height:86px}
.card .btn{font-size:13px;line-height:36px;padding:0 18px;margin-top:14px}

/* benefits */
.benefits{height:631px;color:var(--white)}
.benefits .photo{background:linear-gradient(180deg,rgba(30,36,42,.78),rgba(30,36,42,.7)),linear-gradient(90deg,#4b5560,#6a747e 50%,#3c444c)}
.benefits .section-title{color:var(--white);padding-top:58px}
.benefits .divider span{background:rgba(255,255,255,.5)}
.tabs-row{position:absolute;top:151px;left:142px;display:flex}
.tab{width:227px;height:160px;text-align:center;padding-top:28px;font-size:16px;letter-spacing:1px}
.tab.active{background:rgba(255,255,255,.14)}
.tab svg{display:block;margin:0 auto 30px}
.benefit-band{position:absolute;top:311px;left:0;right:0;height:320px;background:rgba(15,19,23,.6)}
.benefit-grid{position:absolute;top:60px;left:87px;display:grid;grid-template-columns:349px 363px 330px;row-gap:40px}
.benefit h4{display:flex;align-items:center;gap:10px;font-size:21px;font-weight:400}
.benefit p{font-size:13px;line-height:18px;color:#d6dadd;margin:10px 0 0 8px;width:290px}
.tick{width:22px;height:22px;flex:none}

/* technology */
.technology{height:706px;background:#f1f2f4;padding-top:50px}
.catch{text-align:center;color:var(--muted);font-style:italic;font-size:15px;line-height:26px;margin-top:16px}
.tech-tabs{position:absolute;top:218px;left:76px;width:1048px;display:flex}
.tech-tab{width:349px;height:63px;line-height:63px;text-align:center;color:var(--blue);font-size:22px}
.tech-tab.active{background:var(--white)}
.tech-grid{position:absolute;top:281px;left:76px;width:1048px;display:grid;grid-template-columns:repeat(3,1fr);background:var(--white);padding:14px}
.tech-item{padding:22px 20px 18px;height:176px}
.tech-item:nth-child(2),.tech-item:nth-child(4),.tech-item:nth-child(6){background:#f3f4f6}
.tech-item h5{display:flex;align-items:center;gap:12px;font-size:15px;font-weight:400;color:var(--ink)}
.tech-item p{font-size:13px;line-height:19px;color:var(--muted);margin-top:12px}

/* testimonials */
.testimonials{height:529px;color:var(--white)}
.testimonials .photo{background:linear-gradient(180deg,rgba(20,24,28,.72),rgba(20,24,28,.72)),linear-gradient(90deg,#5a5148,#3c4148 30%,#6b6259 60%,#3a3f46)}
.testimonials h2{position:absolute;top:52px;left:0;right:0;text-align:center;font-size:40px;font-weight:700;letter-spacing:1px}
.client{position:absolute;top:118px;left:0;right:0;display:flex;justify-content:center;align-items:center;gap:10px;font-size:20px;font-weight:700}
.client i{width:18px;height:18px;background:#e6007e;display:block}
.testimonials blockquote{position:absolute;top:228px;left:110px;right:110px;text-align:center;font-size:17px;line-height:27px;color:#eceff1}
.dots{position:absolute;top:326px;left:570px;width:60px;border-top:2px dotted #cfd3d6}
.testimonials cite{position:absolute;top:338px;left:0;right:0;text-align:center;font-style:normal;color:var(--blue);font-size:20px}
.avatar{position:absolute;top:380px;left:556px;width:88px;height:88px;border-radius:50%;background:radial-gradient(circle at 50% 40%,#c9cfd6,#7d8893);border:3px solid var(--white)}

/* welcome */
.welcome{height:348px;background:var(--white);text-align:center}
.welcome h2{padding-top:46px;font-size:42px;font-weight:400;color:var(--blue)}
.welcome h2 b{font-weight:900;letter-spacing:2px}
.welcome p{margin:24px auto 0;width:950px;font-size:16px;line-height:24px;color:var(--muted)}
.welcome .btn-solid{position:absolute;top:247px;left:516px;width:168px;height:48px;line-height:48px;padding:0}

/* newsletter */
.newsletter{height:224px;background:var(--white)}
.newsletter .panel{position:absolute;left:0;top:0}
.newsletter h2{position:absolute;top:50px;left:485px;width:520px;text-align:center;font-size:31px;font-weight:400;letter-spacing:1px;color:#222}
.news-form{position:absolute;top:116px;left:485px;display:flex;height:50px}
.news-form .field{width:401px;background:#f5f6f7;border:1px solid var(--line);font-size:14px;color:#777;line-height:48px;padding-left:18px}
.news-form .btn-solid{width:119px;line-height:50px;font-size:15px;text-align:center}

/* contact */
.contact{height:482px;color:var(--white)}
.contact .photo{background:linear-gradient(180deg,rgba(16,20,24,.8),rgba(16,20,24,.82)),linear-gradient(110deg,#3b4249,#59544c 55%,#2e3339)}
.contact h2{position:absolute;top:38px;left:0;right:0;text-align:center;font-size:42px;font-weight:400;color:var(--blue);letter-spacing:1px}
.contact .lead{position:absolute;top:100px;left:270px;right:270px;text-align:center;font-size:16px;line-height:23px;color:#e3e6e8}
.info{position:absolute;top:183px;left:165px;width:330px}
.info-row{display:flex;gap:18px;margin-bottom:22px;font-size:15px;line-height:21px;color:#e3e6e8}
.info-row strong{color:var(--blue);font-weight:400;font-size:19px}
.info-row svg{flex:none;margin-top:2px}
.contact-form{position:absolute;top:183px;left:558px;width:500px}
.input{border:1px solid rgba(255,255,255,.55);height:47px;line-height:45px;padding-left:16px;font-size:14px;color:#e8eaec;margin-bottom:11px;background:rgba(255,255,255,.04)}
.input.area{height:75px;line-height:30px}
.contact-form .btn-solid{width:148px;height:49px;line-height:49px;text-align:center;padding:0;margin-top:4px}

/* footer */
.site-footer{height:107px;background:var(--blue);color:var(--white)}
.site-footer .brand{left:74px;top:34px;font-size:22px;gap:10px;letter-spacing:1px}
.site-footer .brand b{width:30px;height:30px;background:var(--white)}
.foot-nav{position:absolute;top:28px;left:314px;display:flex;gap:22px;font-size:15px;letter-spacing:.5px}
.foot-nav a:first-child{text-decoration:underline}
.copy{position:absolute;top:62px;left:314px;width:572px;text-align:center;font-size:14px}
.copy b{color:#0e3e57}
.social{position:absolute;top:34px;left:946px;display:flex;gap:16px}
.social span{width:48px;height:48px;border-radius:50%;border:2px solid var(--white);display:block}
a{color:inherit;text-decoration:none}
</style>
</head>
<body>

<header class="hero">
  <div class="photo" role="img" aria-label="Photo of colleagues working together in a bright office"></div>
  <div class="brand"><b></b>KELVANBROOK</div>
  <div class="menu-btn"><span></span><span></span><span></span></div>
  <h1>IT SOLUTIONS THAT WORK FOR<br>YOUR BUSINESS.</h1>
  <p>A Full Service Technology Company. Lorem Ipsum is simply dummy text of the printing and typesetting industry. Lorem Ipsum has been the industry's standard dummy text ever since the 1500s.</p>
  <a class="btn" href="#contact">CONTACT US</a>
</header>

<section class="solutions">
  <h2 class="section-title">SOLUTIONS</h2>
  <div class="divider"><span></span><i></i><span></span></div>
  <div class="cards">
    <article class="card">
      <div class="img" role="img" aria-label="Hand touching a glowing IT network interface" style="background:linear-gradient(135deg,#2b6fa8,#7fb7df 60%,#c9dff0)"></div>
      <h3>Managed IT Solutions</h3>
      <p>Our staff will design, service, administer and maintain your IT needs. We are well versed on all major operating system, and network appliances.</p>
      <a class="btn" href="#">CONTACT US</a>
    </article>
    <article class="card">
      <div class="img" role="img" aria-label="Support agent with headset at a laptop" style="background:linear-gradient(135deg,#d8dde2,#8d959c 55%,#3f454b)"></div>
      <h3>Remote Diagnostic &amp; Support</h3>
      <p>Do you need a quick solution to a technical problem? With our live remote assistance tool, a member of our support team can view your desktop and share control of your mouse.</p>
      <a class="btn" href="#">CONTACT US</a>
    </article>
    <article class="card">
      <div class="img" role="img" aria-label="Businessman touching a digital infrastructure display" style="background:linear-gradient(135deg,#0c2a4d,#1f6fb0 55%,#5fc0ee)"></div>
      <h3>IT Infrastructure Design &amp; Installation</h3>
      <p>Do you have more than one site? Do you need remote access? We can design and implement LANS/WANS and VPN's.</p>
      <a class="btn" href="#">CONTACT US</a>
    </article>
  </div>
</section>

<section class="benefits">
  <div class="photo" role="img" aria-label="Blurred photo of a modern glass building interior"></div>
  <h2 class="section-title">BENEFITS</h2>
  <div class="divider"><span></span><i></i><span></span></div>
  <div class="tabs-row">
    <div class="tab active">
      <svg width="60" height="60" viewBox="0 0 60 60" fill="none" stroke="#fff" stroke-width="2"><rect x="6" y="6" width="48" height="48"/><path d="M14 14h32v32H14zM22 22h16v16H22zM14 30h8M38 30h8M30 14v8M30 38v8"/></svg>
      TECHNOLOGY
    </div>
    <div class="tab">
      <svg width="60" height="60" viewBox="0 0 60 60" fill="none" stroke="#fff" stroke-width="2"><circle cx="30" cy="30" r="7"/><circle cx="10" cy="10" r="5"/><circle cx="50" cy="10" r="5"/><circle cx="10" cy="50" r="5"/><circle cx="50" cy="50" r="5"/><path d="M14 14l11 11M46 14L35 25M14 46l11-11M46 46L35 35"/></svg>
      OUTSOURCING
    </div>
    <div class="tab">
      <svg width="60" height="60" viewBox="0 0 60 60" fill="none" stroke="#fff" stroke-width="2"><path d="M6 54h50"/><rect x="10" y="38" width="8" height="16"/><rect x="24" y="28" width="8" height="26"/><rect x="38" y="16" width="8" height="38"/><path d="M8 30L40 6M32 6h8v8"/></svg>
      GROWTH
    </div>
    <div class="tab">
      <svg width="60" height="60" viewBox="0 0 60 60" fill="none" stroke="#fff" stroke-width="2"><circle cx="20" cy="30" r="14"/><path d="M24 24h-6a3 3 0 0 0 0 6h4a3 3 0 0 1 0 6h-6M20 20v4M20 36v4M42 8v44M36 46l6 6 6-6M50 8v30M46 14l4-6 4 6"/></svg>
      COST
    </div>
  </div>
  <div class="benefit-band">
    <div class="benefit-grid">
      <div class="benefit"><h4><svg class="tick" viewBox="0 0 22 22"><circle cx="11" cy="11" r="10" fill="#fff"/><path d="M6 11l3.5 3.5L16 8" stroke="#2a3139" stroke-width="2.4" fill="none"/></svg>In today's world,</h4><p>companies are expected to use technology to function and stay competitive.</p></div>
      <div class="benefit"><h4><svg class="tick" viewBox="0 0 22 22"><circle cx="11" cy="11" r="10" fill="#fff"/><path d="M6 11l3.5 3.5L16 8" stroke="#2a3139" stroke-width="2.4" fill="none"/></svg>However, this aspect</h4><p>of business provides many challenges that most companies cannot solve on their own.</p></div>
      <div class="benefit"><h4><svg class="tick" viewBox="0 0 22 22"><circle cx="11" cy="11" r="10" fill="#fff"/><path d="M6 11l3.5 3.5L16 8" stroke="#2a3139" stroke-width="2.4" fill="none"/></svg>Outsourcing technology</h4><p>provides solutions to almost every aspect of your business and can increase your profits.</p></div>
      <div class="benefit"><h4><svg class="tick" viewBox="0 0 22 22"><circle cx="11" cy="11" r="10" fill="#fff"/><path d="M6 11l3.5 3.5L16 8" stroke="#2a3139" stroke-width="2.4" fill="none"/></svg>Outsourcing can save</h4><p>your business time, effort and can reduce the need for infrastructure and manpower.</p></div>
      <div class="benefit"><h4><svg class="tick" viewBox="0 0 22 22"><circle cx="11" cy="11" r="10" fill="#fff"/><path d="M6 11l3.5 3.5L16 8" stroke="#2a3139" stroke-width="2.4" fill="none"/></svg>Outsourcing removes</h4><p>the burden of an ever-changing infrastructure.</p></div>
      <div class="benefit"><h4><svg class="tick" viewBox="0 0 22 22"><circle cx="11" cy="11" r="10" fill="#fff"/><path d="M6 11l3.5 3.5L16 8" stroke="#2a3139" stroke-width="2.4" fill="none"/></svg>lessen the need for hiring</h4><p>more employees, which in turn will save on all related training costs for your firm.</p></div>
    </div>
  </div>
</section>

<section class="technology">
  <h2 class="section-title">TECHNOLOGY</h2>
  <div class="divider"><span></span><i></i><span></span></div>
  <p class="catch">"Let us worry about your technology…"<br>" so you don't have to!"</p>
  <div class="tech-tabs">
    <div class="tech-tab active">IT SUPPORT SOLUTIONS</div>
    <div class="tech-tab">A Return on Investment</div>
    <div class="tech-tab">Other</div>
  </div>
  <div class="tech-grid">
    <div class="tech-item"><h5><svg width="34" height="30" viewBox="0 0 34 30" fill="none" stroke="#29a8e0" stroke-width="2"><rect x="12" y="2" width="10" height="8"/><rect x="2" y="20" width="10" height="8"/><rect x="22" y="20" width="10" height="8"/><path d="M17 10v5M7 20v-5h20v5"/></svg>Network Administration.</h5><p>Lorem Ipsum is simply dummy text of the printing and typesetting industry. Lorem Ipsum has been the industry's standard dummy text ever since the 1500s.</p></div>
    <div class="tech-item"><h5><svg width="34" height="30" viewBox="0 0 34 30" fill="none" stroke="#29a8e0" stroke-width="2"><rect x="2" y="3" width="30" height="19"/><path d="M12 28h10M17 22v6"/></svg>Desktop Support.</h5><p>Lorem Ipsum is simply dummy text of the printing and typesetting industry. Lorem Ipsum has been the industry's standard dummy text ever since the 1500s.</p></div>
    <div class="tech-item"><h5><svg width="34" height="30" viewBox="0 0 34 30" fill="none" stroke="#29a8e0" stroke-width="2"><rect x="2" y="3" width="24" height="16"/><path d="M10 25h8M14 19v6M26 12h6v14h-8"/></svg>Network Cabling</h5><p>Lorem Ipsum is simply dummy text of the printing and typesetting industry. Lorem Ipsum has been the industry's standard dummy text ever since the 1500s.</p></div>
    <div class="tech-item"><h5><svg width="34" height="30" viewBox="0 0 34 30" fill="none" stroke="#29a8e0" stroke-width="2"><path d="M4 12a19 19 0 0 1 26 0M9 17a12 12 0 0 1 16 0"/><rect x="4" y="21" width="26" height="7"/></svg>Wireless Networks.</h5><p>Lorem Ipsum is simply dummy text of the printing and typesetting industry. Lorem Ipsum has been the industry's standard dummy text ever since the 1500s.</p></div>
    <div class="tech-item"><h5><svg width="34" height="30" viewBox="0 0 34 30" fill="none" stroke="#29a8e0" stroke-width="2"><path d="M17 2l12 4v9c0 7-5 11-12 13C10 26 5 22 5 15V6z"/><path d="M11 15l4 4 8-8"/></svg>Antivirus Solutions.</h5><p>Lorem Ipsum is simply dummy text of the printing and typesetting industry. Lorem Ipsum has been the industry's standard dummy text ever since the 1500s.</p></div>
    <div class="tech-item"><h5><svg width="34" height="30" viewBox="0 0 34 30" fill="none" stroke="#29a8e0" stroke-width="2"><circle cx="17" cy="15" r="12"/><path d="M5 15h24M17 3c-5 6-5 18 0 24M17 3c5 6 5 18 0 24"/></svg>Network Security.</h5><p>Lorem Ipsum is simply dummy text of the printing and typesetting industry. Lorem Ipsum has been the industry's standard dummy text ever since the 1500s.</p></div>
  </div>
</section>

<section class="testimonials">
  <div class="photo" role="img" aria-label="Collage of business portrait photos, darkened"></div>
  <h2>TESTIMONIALS</h2>
  <div class="client"><i></i>Norvale Supply</div>
  <blockquote>" Lorem Ipsum is simply dummy text of the printing and typesetting industry. Lorem Ipsum has been the industry's standard dummy text ever since the 1500s, when an unknown printer took a galley of type and scrambled it to make a type specimen book. "</blockquote>
  <div class="dots"></div>
  <cite>Miles Hartwell</cite>
  <div class="avatar" role="img" aria-label="Portrait photo of the client"></div>
</section>

<section class="welcome">
  <h2>Welcome to <b>KELVANBROOK</b></h2>
  <p>Outsourcing is subcontracting a process, such as product design or manufacturing, to a third-party company.[1] The decision to outsource is often made in the interest of lowering firm costs, redirecting or conserving energy directed at the competencies of a particular business, or to make more efficient use of land, labor, capital, (information) technology and resources. Outsourcing became part of the business lexicon during the 1980s.</p>
  <a class="btn-solid" href="#">READ MORE</a>
</section>

<section class="newsletter">
  <svg class="panel" width="330" height="224" viewBox="0 0 330 224"><polygon points="0,0 330,0 300,224 0,224" fill="#29a8e0"/><polygon points="300,0 330,0 300,224 270,224" fill="#1b8fc4"/></svg>
  <h2>SUBSCRIBE OUR NEWSLETTER</h2>
  <div class="news-form">
    <div class="field">Enter Your Email Here...</div>
    <a class="btn-solid" href="#">SUBSCRIBE</a>
  </div>
</section>

<section class="contact" id="contact">
  <div class="photo" role="img" aria-label="Darkened photo of a laptop on a desk"></div>
  <h2>CONTACT US</h2>
  <p class="lead">Lorem Ipsum is simply dummy text of the printing and typesetting industry. Lorem Ipsum has been the industry's standard dummy text ever since the 1500s.</p>
  <div class="info">
    <div class="info-row"><svg width="20" height="26" viewBox="0 0 20 26"><path d="M10 1a8 8 0 0 0-8 8c0 6 8 16 8 16s8-10 8-16a8 8 0 0 0-8-8z" fill="#29a8e0"/><circle cx="10" cy="9" r="3" fill="#1d2329"/></svg><div><strong>Kelvanbrook Group, Inc.</strong><br>418 Marlow Ave.<br>Dallen,<br>Texas 77031</div></div>
    <div class="info-row"><svg width="20" height="22" viewBox="0 0 20 22"><path d="M4 1l4 5-2 3c1 3 4 6 7 7l3-2 4 4-3 3C9 21 0 12 1 4z" fill="#29a8e0"/></svg><div>(555) 014-2290</div></div>
    <div class="info-row"><svg width="22" height="18" viewBox="0 0 22 18" fill="none" stroke="#29a8e0" stroke-width="2"><rect x="1" y="2" width="20" height="14"/><path d="M1 2l10 8 10-8"/></svg><div>info@kelvanbrook.com</div></div>
  </div>
  <div class="contact-form">
    <div class="input">Name</div>
    <div class="input">E-Mail</div>
    <div class="input area">Message</div>
    <a class="btn-solid" href="#">SUBMIT</a>
  </div>
</section>

<footer class="site-footer">
  <div class="brand"><b></b>KELVANBROOK</div>
  <nav class="foot-nav"><a href="#">HOME</a><a href="#">ABOUT</a><a href="#">SERVICES</a><a href="#">PROJECTS</a><a href="#">SUPPORT</a><a href="#">CAREERS</a><a href="#">CONTACT</a></nav>
  <p class="copy">© <b>Kelvanbrook Group, Inc.</b> - 2017. All Rights Reserved.</p>
  <div class="social"><span></span><span></span><span></span></div>
</footer>

</body>
</html>
```